Velk Partners Building Business Cards

We need a business card that reflects our business as "Solar Experts" in San Diego. Browse our website www.velkpartners.example our License needs to be displayed as "CSLB# 3867140" our phone number is (619) 555-0187

Save thousands on your electric bills and increase the value of your home while helping to protect the environment. Our solar installation experts will help you design the system that's right for you, using only the highest quality equipment that will look great and give you ideal performance. Our goal is to make you energy independent, and get your electric bill to 0.

Paul Osterby
(619) 555-0187
paul@velkpartners.example

Target Market(s)

Home owners in san diego looking for solar

Industry/Entity Type

Solar Energy

Contact Information for Business Card

Paul Osterby
(619) 555-0187
paul@velkpartners.example

Font styles to use
Other font styles liked:
• Use our logo font

Requirements
Must have
• License needs to be displayed as "CSLB# 3867140" our phone number is (619) 555-0187
Nice to have
• Real images of rooftop home solar in san diego
Should not have
• our business address

```html
<!DOCTYPE html>
<html lang="en">
<head>
<meta charset="utf-8">
<title>Velk Partners Building – Business Card</title>
<link rel="stylesheet" href="https://fonts.googleapis.com/css2?family=Roboto:wght@400;500;700&display=swap">
<style>
  :root {
    --backdrop: #2b2b2b;
    --card-white: #ffffff;
    --brand-navy: #1a3c74;
    --brand-gold: #f7ae00;
    --text-grey: #555a60;
    --text-light: #e8edf5;
  }
  html, body {
    margin: 0;
    padding: 0;
    width: 1200px;
    height: 987px;
    overflow: hidden;
    background: var(--backdrop);
    font-family: "Roboto", Arial, sans-serif;
  }
  .canvas {
    position: relative;
    width: 1200px;
    height: 987px;
  }
  .card {
    position: absolute;
    left: 293px;
    width: 615px;
    height: 351px;
    overflow: hidden;
  }
  .card--front { top: 130px; background: var(--card-white); }
  .card--back  { top: 505px; background: var(--brand-navy); }

  .wordmark {
    position: absolute;
    font-weight: 700;
    letter-spacing: -0.5px;
    white-space: nowrap;
  }
  .card--front .wordmark {
    left: 25px;
    top: 30px;
    font-size: 27px;
    color: var(--brand-navy);
  }
  .card--back .wordmark {
    left: 0;
    right: 0;
    top: 138px;
    text-align: center;
    font-size: 40px;
    color: var(--card-white);
  }

  .emblem-area {
    position: absolute;
    left: 240px;
    top: 0;
    width: 375px;
    height: 351px;
    background: linear-gradient(160deg, #fde6a6 0%, #fbd46a 20%, var(--brand-gold) 45%, #2a4d86 72%, var(--brand-navy) 100%);
    clip-path: polygon(110px 0, 100% 0, 100% 100%, 30px 100%, 20px 72%, 0 40%, 40px 15%);
  }

  .licence {
    position: absolute;
    left: 25px;
    top: 221px;
    margin: 0;
    font-size: 15px;
    color: var(--text-grey);
  }
  .contact-list {
    position: absolute;
    left: 25px;
    top: 255px;
    margin: 0;
    padding: 0;
    list-style: none;
    font-size: 14.5px;
    color: var(--text-grey);
  }
  .contact-list li {
    display: flex;
    align-items: center;
    height: 23px;
    white-space: nowrap;
  }
  .contact-list svg {
    width: 14px;
    height: 14px;
    margin-right: 8px;
    fill: var(--brand-navy);
  }

  .holder {
    position: absolute;
    right: 24px;
    top: 268px;
    text-align: right;
    color: var(--card-white);
  }
  .holder__name {
    font-size: 20px;
    font-weight: 500;
    margin: 0;
  }
  .holder__title {
    font-size: 15px;
    margin: 6px 0 0;
  }

  .back-web {
    position: absolute;
    left: 0;
    right: 0;
    top: 293px;
    text-align: center;
    font-size: 14px;
    letter-spacing: 4.5px;
    color: var(--text-light);
  }
</style>
</head>
<body>
<main class="canvas">

  <section class="card card--front" aria-label="Business card front">
    <div class="emblem-area" role="img" aria-label="Large decorative sun rising over a wave, in gold and navy"></div>

    <div class="wordmark">Velk Partners Building</div>

    <p class="licence">CSLB# 3867140</p>

    <ul class="contact-list">
      <li>
        <svg viewBox="0 0 16 16" aria-hidden="true"><path d="M3 2h3l1.5 3.5-2 1.3a8 8 0 0 0 3.7 3.7l1.3-2L14 10v3a1 1 0 0 1-1 1A11 11 0 0 1 2 3a1 1 0 0 1 1-1z"/></svg>
        (619) 555-0187
      </li>
      <li>
        <svg viewBox="0 0 16 16" aria-hidden="true"><path d="M1 3h14v1.2L8 9 1 4.2z"/><path d="M1 5.6 8 10.4l7-4.8V13H1z"/></svg>
        paul@velkpartners.example
      </li>
      <li>
        <svg viewBox="0 0 16 16" aria-hidden="true"><circle cx="8" cy="8" r="7"/></svg>
        www.velkpartners.example
      </li>
    </ul>

    <div class="holder">
      <p class="holder__name">Paul Osterby</p>
      <p class="holder__title">CEO/Founder</p>
    </div>
  </section>

  <section class="card card--back" aria-label="Business card back">
    <div class="wordmark">Velk Partners Building</div>
    <div class="back-web">www.velkpartners.example</div>
  </section>

</main>
</body>
</html>
```